Harrow Point Metrics Company Website Design and Coding

We want to redesign our existing website so that it is more visually and functionally appealing to prospective clients and potential job candidates. We would like to keep our current color scheme and implement our current logo as well. We have a high-level idea of website structure that we are thinking of, which is in the attached files. Logo is included as well. The final design would ideally be energy and analytics focused. We will need the new website to be coded as well, please.

Target Market(s)

Energy and utility industry

Industry/Entity Type

Energy/analytics

Coding

Coded - Design and coding required

Number of Pages Required

5+ page

Font styles to use
Sans Serif

Colors
0094D4
00A9DD
6FCCEA
C7EBF8
E9F6FB
F0912C
F2A743
F7CA91
FBE8D2
FDF5EE

Requirements
Must have
• Consistent color scheme- please use the one that we provided. We need an overview, a home page, and our core services. A separate job application page. Logo must be incorporated. We would like e "Meet our Team" page. Please include all of the content that is listed in our attachments.
Nice to have
• Movement
Should not have
• No music, no cartoons/animation, no pictures of a chalkboard

```html
<!DOCTYPE html>
<html lang="en">
<head>
<meta charset="utf-8">
<title>Harrow Point Metrics</title>
<link href="https://fonts.googleapis.com/css2?family=Barlow:wght@500;600;700&family=Roboto:wght@400;500;700&display=swap" rel="stylesheet">
<style>
:root{
  --blue:#0094D4; --blue-2:#00A9DD; --blue-3:#6FCCEA; --blue-4:#C7EBF8; --blue-5:#E9F6FB;
  --navy:#0B4DA6; --ink:#111; --body:#444; --gray-bg:#F4F4F4;
  --orange:#F0912C; --orange-2:#F2A743; --orange-3:#F7CA91; --orange-hot:#F57A0B;
  --dark:#0a0a0a;
}
*{box-sizing:border-box;margin:0;padding:0}
html,body{width:1200px;height:4438px;overflow:hidden}
body{position:relative;background:#fff;font-family:"Roboto",Arial,sans-serif;color:var(--body)}
.abs{position:absolute}
h1,h2,h3,h4,.btn{font-family:"Barlow",Arial,sans-serif}
a{color:inherit;text-decoration:none}
.btn{position:absolute;display:flex;align-items:center;justify-content:center;border-radius:30px;font-weight:700;font-size:14px;color:#fff}
.btn-orange{background:var(--orange-hot)}
.btn-navy{background:var(--navy)}

/* header */
.topnav{left:0;top:0;width:1200px;height:35px;display:flex;gap:30px;padding-left:124px;align-items:center;font-size:12.5px;color:#222}
.brand{display:flex;align-items:center;gap:12px;font-family:"Roboto",sans-serif;font-weight:400;font-size:28px;color:var(--blue)}
.brand .dot{width:34px;height:34px;border-radius:50%;border:2px solid var(--blue-3)}
.header-brand{left:112px;top:54px}
.mainnav{left:500px;top:69px;width:700px;height:53px;background:var(--orange-hot);clip-path:polygon(22px 0,100% 0,100% 100%,0 100%);display:flex;gap:44px;align-items:center;padding-left:76px;font-size:15px;color:#fff}

/* hero */
.hero{left:0;top:122px;width:1200px;height:670px;background:radial-gradient(ellipse at 70% 45%,#1d6fd1 0%,#0b2f78 40%,#06163e 75%)}
.hero-wave{left:0;top:700px}
.hero-title{left:112px;top:284px;font-size:50px;line-height:60px;font-weight:700;color:#fff;letter-spacing:.5px}
.hero-title span{color:var(--orange-hot)}
.hero-text{left:112px;top:412px;width:520px;font-size:14px;line-height:26px;color:#fff}
.hero-btn{left:112px;top:515px;width:164px;height:56px;background:var(--blue);font-size:14px}

/* section titles */
.sec-title{left:0;width:1200px;text-align:center;font-family:"Barlow",sans-serif;font-weight:700;font-size:36px;color:var(--ink)}

/* services */
.svc{width:312px;height:464px;border:2px solid var(--orange-hot);border-radius:28px;padding:30px 24px 0 24px;background:#fff}
.svc.feature{border:none;background:linear-gradient(180deg,#F28F2E 0%,#E99B5A 45%,#3E8ED8 80%,#1C8CE0 100%);color:#fff}
.svc svg{display:block;margin-bottom:26px}
.svc h3{font-size:21px;font-weight:700;line-height:26px;color:var(--ink);margin-bottom:14px}
.svc.feature h3{color:#fff}
.svc p{font-size:13.5px;line-height:26px;color:#333}
.svc.feature p{color:#fff}
.svc .more{display:inline-block;margin:10px 0 0 4px;font-size:14px;color:var(--orange-hot);text-decoration:underline}
.svc.feature .more{color:#fff}

/* research */
.research-bg{left:0;top:1624px;width:1200px;height:504px;background:var(--gray-bg)}
.research-img{left:138px;top:1696px;width:441px;height:348px;border-radius:40px;background:linear-gradient(135deg,#3a3f46 0%,#9aa0a6 45%,#d9d4cc 70%,#e38a2e 100%)}
.research-copy{left:610px;top:1710px;width:480px}
.research-copy h2{font-size:35px;font-weight:600;color:var(--ink);margin-bottom:14px}
.research-copy h4{font-size:20px;font-weight:600;color:var(--navy);margin-bottom:8px}
.research-copy p{font-size:14px;line-height:26px;color:#333;margin-bottom:18px}

/* overview */
.overview-text{left:150px;top:2266px;width:900px;text-align:center;font-size:14px;line-height:26px;color:#333}

/* case studies */
.cases{left:0;top:2531px;width:1200px;height:627px;background:linear-gradient(180deg,#1477d6 0%,#1d86de 60%,#1a7fd8 100%)}
.cases .sec-title{color:#fff;top:70px;font-weight:600}
.case{position:absolute;top:164px;width:205px;text-align:center}
.case .thumb{width:205px;height:205px;border-radius:12px}
.case h4{margin-top:16px;font-size:21px;font-weight:600;line-height:26px;color:#fff}

/* team */
.member{top:3344px;width:207px;height:324px;background:#fff;box-shadow:0 4px 14px rgba(0,0,0,.12);text-align:center;padding-top:118px}
.avatar{position:absolute;left:49px;top:-22px;width:110px;height:110px;border-radius:50%;border:3px solid #fff;background:linear-gradient(160deg,#6c6f74,#2a2d31)}
.member h4{font-size:18px;font-weight:600;color:var(--blue)}
.member .role{font-size:13px;color:#777;margin:8px 0 14px}
.member p{font-size:13px;line-height:26px;color:#333;padding:0 14px;height:104px;overflow:hidden}
.member .go{position:absolute;left:86px;bottom:-6px;width:36px;height:36px;border-radius:50%;background:var(--blue);display:flex;align-items:center;justify-content:center}

/* careers + footer */
.careers{left:0;top:3761px;width:1200px;height:677px;background:linear-gradient(120deg,#F07A10 0%,#F28A2A 60%,#E8781A 100%)}
.careers h2{position:absolute;left:110px;top:36px;font-size:38px;font-weight:600;color:#fff}
.careers p{position:absolute;left:110px;top:84px;width:790px;font-size:13.5px;line-height:26px;color:#fff}
.careers .btn{left:921px;top:132px;width:167px;height:57px;background:var(--navy)}
.footer-shape{left:0;top:3950px}
.footer-brand{left:110px;top:4094px;font-size:23px}
.social{left:186px;top:4165px;display:flex;gap:10px}
.social span{width:28px;height:28px;border-radius:50%;background:#fff}
.social span:first-child{background:var(--orange-hot)}
.fcol{top:4092px}
.fcol h4{font-size:21px;font-weight:600;color:#fff;margin-bottom:14px}
.fcol li{list-style:none;font-size:14px;color:#fff;line-height:30px}
.fcol li::before{content:"«";margin-right:8px}
.news-input{left:811px;top:4136px;width:279px;height:40px;border:1px solid #555;border-radius:4px;color:#888;font-size:14px;padding:11px 16px}
.news-btn{left:811px;top:4190px;width:279px;height:39px;border-radius:4px;background:var(--blue);font-size:14px}
.copy{left:0;top:4372px;width:1200px;text-align:center;font-size:14px;color:#fff}
</style>
</head>
<body>

<nav class="abs topnav">
  <a>Forecating &amp; Perdictive Analytics</a><a>T&amp;D Planning</a><a>Evaluation</a><a>Pilot&amp; Emerging Tech Support</a><a>Program &amp; Portfolio Resource Planning</a><a>more</a>
</nav>
<div class="abs brand header-brand"><span class="dot"></span>Harrow Point Metrics</div>
<nav class="abs mainnav"><a>Core Services</a><a>About</a><a>Our Work</a><a>Blog</a><a>Contatc Us</a></nav>

<section class="abs hero" role="img" aria-label="Blue financial data chart with glowing bars and curves"></section>
<svg class="abs hero-wave" width="1200" height="100" viewBox="0 0 1200 100">
  <path d="M0 40 Q600 110 1200 10 L1200 100 L0 100Z" fill="#fff"/>
  <path d="M0 40 Q600 110 1200 10 L1200 34 Q600 120 0 70Z" fill="#F57A0B"/>
  <path d="M0 70 Q600 120 1200 34 L1200 40 Q600 126 0 78Z" fill="#0094D4"/>
</svg>
<h1 class="abs hero-title"><span>WELCOME TO</span><br>HARROW POINT METRICS</h1>
<p class="abs hero-text">Harrow Point Metrics was formed in 2016 to help utilities and regulatory agencies navigate the technical, economic, and policy challenges of build-ing a smarter and cleaner energy future.</p>
<a class="btn hero-btn">GET STARTED</a>

<h2 class="abs sec-title" style="top:910px">OUR SERVICES</h2>
<article class="abs svc" style="left:112px;top:988px">
  <svg width="110" height="110" viewBox="0 0 110 110" fill="none" stroke="#0094D4" stroke-width="3"><circle cx="62" cy="46" r="34"/><path d="M38 70 L10 98" stroke-width="8"/><path d="M48 62V44M60 62V30M72 62V38"/></svg>
  <h3>Predictive Analytics<br>and Forecasting</h3>
  <p>Distributed energy resource integra-tion into planning and operations Granular analysis (8760) and fore-casting of distributed energy resource adoption and impacts on the grid, in-cluding solar, battery storage...</p>
  <a class="more">Learn More</a>
</article>
<article class="abs svc feature" style="left:443px;top:988px">
  <svg width="110" height="110" viewBox="0 0 110 110" fill="none" stroke="#fff" stroke-width="3"><rect x="8" y="10" width="80" height="64" rx="4"/><path d="M8 22H88"/><circle cx="66" cy="64" r="22"/><path d="M82 80L100 98" stroke-width="6"/><path d="M56 72V60M64 72V52M72 72V58"/></svg>
  <h3>T&amp;D Plannin</h3>
  <p>Location specific, probabilistic fore-casting for system, transmission and distribution planning (electric and gas) Non-wire alternative and non-pipe alternative project assess-ments and optimization Expert testi-mony</p>
  <a class="more">Learn More</a>
</article>
<article class="abs svc" style="left:775px;top:988px">
  <svg width="110" height="110" viewBox="0 0 110 110" fill="none" stroke="#0094D4" stroke-width="3"><rect x="14" y="6" width="62" height="94" rx="4"/><path d="M24 24l5 5 9-10M24 48l5 5 9-10M24 72l5 5 9-10M46 26H66M46 50H66M46 74H62"/><path d="M90 40L66 96" stroke-width="5"/></svg>
  <h3>Evaluation</h3>
  <p>Demand Response evaluations Behavioral program evaluations Energy Efficiency evaluations Time-varying rate evaluations Process and outcome evaluations Pilot research design and evaluation Ability to provide real-time evaluation</p>
  <a class="more">Learn More</a>
</article>
<a class="btn btn-orange" style="left:529px;top:1498px;width:143px;height:54px">View All</a>

<div class="abs research-bg"></div>
<div class="abs research-img" role="img" aria-label="Hand over laptop with rising bar chart overlay"></div>
<div class="abs research-copy">
  <h2>RESEARCH AND ANALYSIS</h2>
  <h4>Journal Articles and Conference Presentations</h4>
  <p>Links to relevant published journal articles and conference presentations</p>
  <h4>Published Reports</h4>
  <p>Links to published reports</p>
</div>
<a class="btn btn-navy" style="left:608px;top:1954px;width:167px;height:56px">Learn More</a>

<h2 class="abs sec-title" style="top:2203px">COMPANY OVERVIEW</h2>
<p class="abs overview-text">Harrow Point Metrics (HPM) was formed in 2016 to help utilities and regulatory agencies navigate the technical, economic, and policy challenges of building a smarter and cleaner energy future. Our research focuses on impact analysis as well as predictive and causal analytics. We deliver data-driven insights into how various technologies and interventions affect the way homes and businesses use energy and how those in turn affect grid and system planning.</p>
<a class="btn btn-navy" style="left:523px;top:2395px;width:154px;height:57px">Learn More</a>

<section class="abs cases">
  <h2 class="sec-title abs">PROPOSED CASE STUDIES FOR EACH CORE SERVICE</h2>
  <div class="case" style="left:114px"><div class="thumb" role="img" aria-label="Desk with printed charts and laptop" style="background:linear-gradient(135deg,#c9ccd0,#f2f2f2 50%,#8f9aa6)"></div><h4>Predictive Analytics and Forecasting</h4></div>
  <div class="case" style="left:368px"><div class="thumb" role="img" aria-label="Blue glowing line and bar chart" style="background:linear-gradient(135deg,#0a2550,#135fb8 60%,#082046)"></div><h4>T&amp;D Planning</h4></div>
  <div class="case" style="left:622px"><div class="thumb" role="img" aria-label="Hand pointing at trading data screen" style="background:linear-gradient(135deg,#0d1a22,#1f4e5a 55%,#0a1418)"></div><h4>Evaluation</h4></div>
  <div class="case" style="left:876px"><div class="thumb" role="img" aria-label="Digital analytics icons on dark blue" style="background:radial-gradient(circle at 50% 50%,#3a86e0,#0d2a5c 70%)"></div><h4>Pilot &amp; Emerging Tech Support</h4></div>
  <a class="btn btn-orange" style="left:523px;top:486px;width:154px;height:55px">Learn More</a>
</section>

<h2 class="abs sec-title" style="top:3238px">OUR TEAM</h2>
<article class="abs member" style="left:110px"><div class="avatar" role="img" aria-label="Portrait photo of team member"></div><h4>Evan Marsh, M.S.</h4><div class="role">Partner</div><p>Evan Marsh is an applied statistician whose work is centered around estimating the impacts of demand</p><span class="go"><svg width="14" height="14" viewBox="0 0 14 14"><path d="M2 7H12M8 3l4 4-4 4" stroke="#fff" stroke-width="2" fill="none"/></svg></span></article>
<article class="abs member" style="left:367px"><div class="avatar" role="img" aria-label="Portrait photo of team member"></div><h4>Daniel Okafor, M.P.P.</h4><div class="role">Partner</div><p>Daniel Okafor specializes in ad-vanced applications of data analytics using large volumes of hourly and sub-hourly</p><span class="go"><svg width="14" height="14" viewBox="0 0 14 14"><path d="M2 7H12M8 3l4 4-4 4" stroke="#fff" stroke-width="2" fill="none"/></svg></span></article>
<article class="abs member" style="left:625px"><div class="avatar" role="img" aria-label="Portrait photo of team member"></div><h4>Laura Brennick</h4><div class="role">Partner</div><p>Ms. Brennick's work has focused an array of Distribut-ed Energy Resources (DERs) from solar photo-voltaic to</p><span class="go"><svg width="14" height="14" viewBox="0 0 14 14"><path d="M2 7H12M8 3l4 4-4 4" stroke="#fff" stroke-width="2" fill="none"/></svg></span></article>
<article class="abs member" style="left:882px"><div class="avatar" role="img" aria-label="Portrait photo of team member"></div><h4>Miriam Castellan, M.S.</h4><div class="role">Partner</div><p>Ms. Castellan has extensive expertise with analysis of smart meter data, rate design,</p><span class="go"><svg width="14" height="14" viewBox="0 0 14 14"><path d="M2 7H12M8 3l4 4-4 4" stroke="#fff" stroke-width="2" fill="none"/></svg></span></article>

<section class="abs careers">
  <h2>CAREERS</h2>
  <p>At HPM, we are driven to help create a smarter and cleaner energy future, and we are always looking for talented professionals who share our passion for achieving this goal. We are a transparent organization where you will have the opportunity to work directly with our senior energy experts. Our employees get to work on a wide variety of projects and develop new skills so that they are well equipped to interact with our clients find effective ways to solve our clients' problems.</p>
  <a class="btn">Learn More</a>
</section>
<svg class="abs footer-shape" width="1200" height="488" viewBox="0 0 1200 488">
  <path d="M0 110 Q420 20 800 30 Q1050 36 1200 0 L1200 488 L0 488Z" fill="#0a0a0a"/>
</svg>
<div class="abs brand footer-brand"><span class="dot"></span>Harrow Point Metrics</div>
<div class="abs social"><span></span><span></span><span></span><span></span></div>
<div class="abs fcol" style="left:444px"><h4>QUICK LINKS</h4><ul><li>Core Services</li><li>About</li><li>Our Work</li><li>Blog</li><li>Contatc Us</li></ul></div>
<div class="abs fcol" style="left:620px"><h4>HELP LINKS</h4><ul><li>Terms&amp;conditions</li><li>Privacy Policy</li><li>About Us</li><li>Support</li></ul></div>
<div class="abs fcol" style="left:811px"><h4>GET OUR NEWSLETTER</h4></div>
<div class="abs news-input">Enter Your Email</div>
<a class="btn news-btn">SUBSCRIBE NOW</a>
<p class="abs copy">©Copyrights 2022 Harrow Point Metrics | &nbsp; All Rights Reserved</p>

</body>
</html>
```